Business Card for Air Cargo Brokerage

Hi Craftquorum -

Please see the images attached. I need a business card with a similar image and format but modernized. Business card should be portrait and have room for a QR code.

Thanks

```html
<!DOCTYPE html>
<html lang="en">
<head>
<meta charset="utf-8">
<title>Skyline Air Freight – Business Card</title>
<link href="https://fonts.googleapis.com/css2?family=Poppins:wght@300;400;600;800&family=Open+Sans:wght@500&display=swap" rel="stylesheet">
<style>
  :root {
    --stage: #222222;
    --pattern-light: #3a3b40;
    --pattern-mid: #202125;
    --pattern-dark: #0c0d0f;
    --card-light: #ffffff;
    --ink: #0d0d0d;
    --ink-soft: #2b2b2b;
  }
  * { box-sizing: border-box; margin: 0; padding: 0; }
  html, body { width: 1200px; height: 711px; overflow: hidden; background: var(--stage); }
  .canvas {
    position: relative; width: 1200px; height: 711px;
    display: flex; justify-content: center; align-items: center; gap: 60px;
  }
  .card {
    width: 310px; height: 542px; border-radius: 22px; position: relative; overflow: hidden;
  }
  .card--back { background: var(--pattern-dark); }
  .card--back .pattern-area {
    position: absolute; inset: 0;
    background: linear-gradient(165deg, var(--pattern-light) 0%, var(--pattern-mid) 45%, var(--pattern-dark) 100%);
  }
  .card--front {
    background: var(--card-light); color: var(--ink);
    display: flex; flex-direction: column; align-items: center; text-align: center;
    padding-top: 78px;
    font-family: "Poppins", sans-serif;
  }
  .brand { display: flex; flex-direction: column; align-items: center; }
  .brand__mark { width: 22px; height: 22px; background: var(--ink); margin-bottom: 14px; }
  .brand__name { font-weight: 800; font-size: 26px; letter-spacing: -0.3px; line-height: 1.1; }
  .brand__tagline {
    font-family: "Open Sans", sans-serif; font-weight: 500; font-size: 10.5px;
    letter-spacing: 0.6px; margin-top: 8px; color: var(--ink-soft);
  }
  .person { margin-top: 92px; }
  .person__name { font-size: 26px; line-height: 1.1; }
  .person__first { font-weight: 800; }
  .person__last { font-weight: 300; }
  .person__title { font-weight: 600; font-size: 12.5px; margin-top: 2px; }
  .divider { display: flex; align-items: center; gap: 6px; margin-top: 16px; width: 230px; }
  .divider__line { flex: 1; height: 1.5px; background: var(--ink); }
  .divider__icons { display: flex; gap: 4px; }
  .icon { width: 20px; height: 20px; background: var(--ink); border-radius: 3px; display: flex; align-items: center; justify-content: center; }
  .contact { margin-top: 12px; font-size: 13.5px; line-height: 1.55; font-weight: 400; font-style: normal; }
</style>
</head>
<body>
<main class="canvas">
  <section class="card card--back">
    <div class="pattern-area" role="img" aria-label="Repeating embossed pattern of small cargo plane silhouettes, lighter grey at the top fading to black, with one white plane accent near the lower right"></div>
  </section>

  <section class="card card--front">
    <div class="brand">
      <span class="brand__mark"></span>
      <h1 class="brand__name">Skyline Air Freight</h1>
      <p class="brand__tagline">SOLUTIONS FOR GLOBAL AIR COMMERCE</p>
    </div>

    <div class="person">
      <h2 class="person__name"><span class="person__first">Marta</span> <span class="person__last">Novakova</span></h2>
      <p class="person__title">Managing Director</p>
    </div>

    <div class="divider">
      <span class="divider__line"></span>
      <div class="divider__icons">
        <span class="icon"><svg width="12" height="12" viewBox="0 0 24 24" fill="#fff"><path d="M6.6 10.8a15 15 0 0 0 6.6 6.6l2.2-2.2a1 1 0 0 1 1-.25 11.4 11.4 0 0 0 3.6.57 1 1 0 0 1 1 1V20a1 1 0 0 1-1 1A17 17 0 0 1 3 4a1 1 0 0 1 1-1h3.5a1 1 0 0 1 1 1c0 1.25.2 2.45.57 3.57a1 1 0 0 1-.25 1z"/></svg></span>
        <span class="icon"><svg width="13" height="10" viewBox="0 0 26 20" fill="none" stroke="#fff" stroke-width="2"><rect x="1" y="1" width="24" height="18"/><path d="M1 1l12 10L25 1"/></svg></span>
        <span class="icon"><svg width="12" height="12" viewBox="0 0 24 24" fill="none" stroke="#fff" stroke-width="2"><circle cx="12" cy="12" r="10"/><path d="M2 12h20M12 2a15 15 0 0 1 0 20M12 2a15 15 0 0 0 0 20"/></svg></span>
      </div>
      <span class="divider__line"></span>
    </div>

    <address class="contact">
      <p>(555) 014-2287</p>
      <p>hello@skylineair.example</p>
      <p>www.skylineair.example</p>
    </address>
  </section>
</main>
</body>
</html>
```